New Dental Office Needs an Attractive and user friendly Website Designed

I need a website for a new dental office. The Name is Harrowfield Dentistry. I would like a Modern design with a user friendly interface and usability.
I would like a landing page, a page that lists the services we offer: Cosmetic Dentistry, Implants, Dental Hygiene, Emergency Services, Restorations, Dentures
Target Market(s)
Mid to upper class
Industry/Entity Type
Dentistry
Coding
Number of Pages Required
1 page
Requirements
Must have
- Landing page that has a scheduling option, Procedures, operating hours, and contact us info
Nice to have
- Appealing design, Soft comforting colors. Easy to navigate page, Modern and professional.

```html
<!DOCTYPE html>
<html lang="en">
<head>
<meta charset="utf-8">
<title>Harrowfield Dentistry</title>
<link href="https://fonts.googleapis.com/css2?family=Plus+Jakarta+Sans:wght@400;500;600;700&display=swap" rel="stylesheet">
<style>
:root{
  --board:#4d4d4d;
  --teal:#0f676b;
  --teal-dark:#0c5a5e;
  --accent:#13909c;
  --ink:#163c57;
  --text:#5f6b73;
  --soft:#eef4f3;
  --card:#f5f7f7;
  --white:#ffffff;
  --photo-warm:#c9a894;
  --photo-cool:#9fb9c3;
}
*{margin:0;padding:0;box-sizing:border-box}
html,body{width:747px;height:1200px;overflow:hidden}
body{background:var(--board);font-family:"Plus Jakarta Sans",Arial,sans-serif;color:var(--ink);position:relative;font-size:4px;line-height:1.4}
.col{position:absolute;overflow:hidden;background:var(--white)}
.col-left{left:30px;top:26px;width:328px;height:1174px}
.col-right{left:387px;top:0;width:327px;height:1200px}
.abs{position:absolute}
.photo{position:absolute;background:linear-gradient(135deg,var(--photo-cool),var(--photo-warm))}
.band{position:absolute;left:0;width:100%}
.soft{background:var(--soft)}
.eyebrow{font-size:3.6px;color:var(--ink);font-weight:500}
.h2{font-size:10px;font-weight:600;color:var(--ink);line-height:1.2}
.small{font-size:3.4px;color:var(--text);line-height:1.6}
.btn{position:absolute;font-size:3.6px;font-weight:500;display:flex;align-items:center;justify-content:center;border-radius:2px}
.nav{top:0;height:19px;background:var(--white)}
.brand{position:absolute;font-weight:700;color:var(--ink);font-size:6px;letter-spacing:.1px}
.nav-links{position:absolute;left:93px;top:7px;display:flex;gap:6px;font-size:3.6px;color:var(--ink)}
.hero{top:18px;height:166px;background:var(--teal);overflow:hidden}
.hero-photo{left:150px;top:0;width:178px;height:166px;background:linear-gradient(120deg,#1f7b7e 0%,#8fb6b3 45%,#d7b59f 80%,#b08269 100%)}
.hero-copy{position:absolute;left:21px;top:31px;color:var(--white);width:135px}
.hero-copy h1{font-size:15px;font-weight:500;line-height:1.18;margin:3px 0 4px}
.hero-copy p{font-size:3.8px;line-height:1.75;opacity:.92}
.cta-card{left:212px;top:151px;width:96px;height:70px;background:var(--teal-dark);border-radius:4px 4px 0 0;color:var(--white);padding:9px 9px}
.stats{top:184px;height:37px;background:var(--soft)}
.svc-row{position:absolute;left:19px;width:289px;height:35px;border-bottom:.5px solid #d7e2e1;display:flex;align-items:center}
.svc-num{width:15px;font-size:3px;color:var(--ink);transform:rotate(-90deg)}
.svc-name{width:108px;font-size:7.2px;font-weight:500;color:var(--ink)}
.svc-desc{width:100px;font-size:3.4px;color:var(--text);line-height:1.6}
.arrow-dot{position:absolute;right:3px;width:12px;height:12px;border-radius:50%;background:var(--white);display:flex;align-items:center;justify-content:center;font-size:5px;color:var(--accent)}
.pager{position:absolute;top:696px;left:130px;display:flex;gap:5px}
.pager span{width:10px;height:10px;border-radius:50%;background:var(--white);font-size:3.2px;display:flex;align-items:center;justify-content:center}
.pager .on{background:var(--accent);color:var(--white)}
.stat{position:absolute;width:66px;height:64px;border-radius:5px;background:var(--card);padding:7px 8px}
.stat .lbl{font-size:5.4px;color:var(--text);line-height:1.3}
.stat .num{position:absolute;left:8px;bottom:6px;font-size:11px;font-weight:500;color:var(--ink)}
.stat.pic{padding:0;overflow:hidden}
.member{position:absolute;width:70px;text-align:center;font-size:4px;line-height:1.3}
.member .av{width:34px;height:34px;border-radius:50%;margin:0 auto 3px;background:linear-gradient(160deg,#8aa2b3,#6b5547)}
.member b{display:block;font-size:4px;font-weight:500;color:var(--ink)}
.member i{display:block;font-style:normal;font-size:2.8px;color:var(--accent);margin-top:1px}
.faq{position:absolute;left:167px;top:230px;width:141px;height:167px;background:var(--white);border-radius:5px;padding:9px 9px}
.faq-q{font-size:4.6px;color:var(--ink);display:flex;justify-content:space-between;padding:7px 0 8px;border-top:.5px solid #e1e8e8}
.footer{left:19px;top:1075px;width:289px;height:113px;background:var(--teal);border-radius:5px;color:var(--white);padding:11px 15px}
.footer h4{font-size:4.4px;font-weight:600;margin-bottom:6px}
.footer .list{font-size:3.4px;line-height:2.8}
.field{position:absolute;height:13px;background:var(--white);border:.5px solid #e0e7e7;border-radius:2px;font-size:3.2px;color:#b1b9bd;padding:0 4px;display:flex;align-items:center;justify-content:space-between}
.flabel{position:absolute;font-size:3.4px;color:var(--ink)}
</style>
</head>
<body>

<section class="col col-left">
  <header class="band nav">
    <div class="brand" style="left:21px;top:5px">Harrowfield</div>
    <nav class="nav-links"><span>Home</span><span>About us</span><span>Services</span><span>Testimonials</span><span>Case studies</span><span>Gallery</span><span>Blogs</span></nav>
    <div class="btn" style="left:276px;top:4px;width:30px;height:10px;background:var(--accent);color:var(--white)">Contact Us</div>
  </header>

  <div class="band hero">
    <div class="photo hero-photo" role="img" aria-label="Dentist in a mask smiling with a young woman patient in the chair"></div>
    <div class="hero-copy">
      <div style="font-size:3.8px">Welcome to the Harrowfield</div>
      <h1>Get your confident smile now!</h1>
      <p>At our practice, excellence in dentistry goes hand-in-hand with personalized care, offering patients of all ages a wide range of tailored dental solutions.</p>
    </div>
    <div class="btn" style="left:21px;top:103px;width:50px;height:10px;background:var(--white);color:var(--ink)">Book an appointment</div>
    <div class="abs" style="left:21px;top:133px;width:140px;height:.5px;background:rgba(255,255,255,.25)"></div>
    <div class="abs" style="left:21px;top:135px;font-size:3.8px;color:var(--white)">ReviewHub Rating <span style="color:#f3b53b">5.0 ★★★★★</span> based on 492 reviews</div>
  </div>

  <div class="band stats">
    <div class="abs" style="left:19px;top:7px;font-size:14px;font-weight:500;color:var(--ink)">8k+</div>
    <div class="abs" style="left:19px;top:26px;font-size:3.8px;color:var(--ink)">Happy Patients</div>
    <div class="abs" style="left:58px;top:8px;width:.5px;height:22px;background:#c9d6d5"></div>
    <div class="abs small" style="left:65px;top:10px;width:110px">Let's bring your perfect smile to life! Whether you need a complete smile makeover or routine dental care, we've got you covered.</div>
  </div>
  <div class="abs cta-card">
    <div style="font-size:5px;font-weight:600;line-height:1.4">Ready for a Stunning Smile Transformation?</div>
    <div style="font-size:3.4px;line-height:1.7;margin-top:5px;opacity:.85">Book an appointment today and let us help you achieve the healthy, beautiful smile you deserve!</div>
    <div style="position:absolute;left:9px;bottom:9px;font-size:4px;font-weight:600">Book an Appointment</div>
    <svg class="abs" style="right:9px;bottom:8px" width="8" height="8" viewBox="0 0 8 8"><circle cx="4" cy="4" r="4" fill="#fff"/><path d="M2.3 4h3.2M4.2 2.7 5.5 4 4.2 5.3" stroke="#0c5a5e" stroke-width=".7" fill="none"/></svg>
  </div>

  <!-- about -->
  <div class="abs" style="left:46px;top:326px;width:34px;height:46px;border-radius:12px;background:#f4f7f8" role="img" aria-label="Faint decorative tooth outline"></div>
  <div class="photo" style="left:19px;top:251px;width:77px;height:44px;border-radius:22px" role="img" aria-label="Dentist treating a patient in the clinic"></div>
  <div class="photo" style="left:76px;top:274px;width:76px;height:112px;border-radius:38px;background:linear-gradient(160deg,#c7d2d6,#8f6d5c);border:2px solid #fff" role="img" aria-label="Smiling dental assistant in a mask and white coat"></div>
  <div class="abs" style="left:104px;top:250px;font-size:12px;font-weight:500;line-height:1.2">10+</div>
  <div class="abs" style="left:129px;top:252px;font-size:3.6px;line-height:1.7">Years of<br>Experience</div>
  <div class="abs" style="left:174px;top:243px;font-size:15px;font-weight:700;color:#f4f6f6;line-height:1">About Us</div>
  <div class="abs eyebrow" style="left:175px;top:251px">About Us</div>
  <div class="abs h2" style="left:174px;top:265px;font-size:12px;width:140px">Welcome to Harrowfield Dentistry!</div>
  <div class="abs small" style="left:174px;top:302px;width:135px">We are on a mission to bring smile on people's face since 2011. Harrowfield Dentistry is conveniently located in Los Angeles where we make sure that we provide our patients with best facilities and a seamless dentistry experience.</div>
  <div class="abs" style="left:174px;top:335px;font-size:3.6px;color:var(--ink);line-height:1.45;width:115px">
    <div style="margin-bottom:3px">● Advanced Technology For Optimal Patient Comfort.</div>
    <div style="margin-bottom:3px">● Happy Patients From Los Angeles, USA, And Around The World</div>
    <div style="margin-bottom:3px">● Expert Teams In Preventive And Curative Dentistry.</div>
    <div>● Focus On Aesthetic Value In All Treatments.</div>
  </div>
  <div class="photo" style="left:174px;top:382px;width:14px;height:14px;border-radius:2px" role="img" aria-label="Portrait of the practice owner"></div>
  <div class="abs" style="left:192px;top:383px;font-size:4.6px;font-weight:500">Dr. Dorian Whitcombe</div>
  <div class="abs" style="left:192px;top:391px;font-size:3.4px;color:var(--text)">Owner and Director</div>

  <!-- services -->
  <div class="band soft" style="top:418px;height:311px"></div>
  <div class="abs" style="left:0;width:328px;top:440px;text-align:center;font-size:10px;font-weight:500">Enjoy Specialized Dental Services</div>
  <div class="svc-row" style="top:461px"><span class="svc-num">1</span><span class="svc-name">Dental Implants</span><span class="svc-desc">The implant is a medical device made of titanium which serves as the root for missing tooth on top of...</span><span class="arrow-dot">↗</span></div>
  <div class="abs" style="left:23px;top:505px;width:282px;height:36px;background:var(--white);border-radius:4px"></div>
  <div class="svc-row" style="top:505px;border:none;left:23px"><span class="svc-num">2</span><span class="svc-name" style="color:var(--accent);width:82px">Cosmetic Dentistry</span><span class="abs" style="left:91px;top:11px;width:13px;height:13px;border-radius:50%;background:var(--accent);color:#fff;font-size:5px;display:flex;align-items:center;justify-content:center">↗</span><span class="svc-desc" style="margin-left:22px">The implant is a medical device made of titanium which serves as the root for missing tooth on top of...</span></div>
  <div class="photo" style="left:250px;top:508px;width:50px;height:29px;border-radius:15px" role="img" aria-label="Dentist examining a smiling patient"></div>
  <div class="svc-row" style="top:549px"><span class="svc-num">3</span><span class="svc-name">Dental Hygiene</span><span class="svc-desc">Bleeding gums when brushing is common but not normal and should never be ignored. It may indicate...</span><span class="arrow-dot">↗</span></div>
  <div class="svc-row" style="top:584px"><span class="svc-num">4</span><span class="svc-name">Emergency Services</span><span class="svc-desc">Tooth colored resin-based light-cured cement which bonds to the tooth surface. We try and do co...</span><span class="arrow-dot">↗</span></div>
  <div class="svc-row" style="top:619px"><span class="svc-num">5</span><span class="svc-name">Restorations</span><span class="svc-desc">Tooth pain is the 2nd most unbearable pain. It can be caused due to many reasons.</span><span class="arrow-dot">↗</span></div>
  <div class="svc-row" style="top:654px"><span class="svc-num">6</span><span class="svc-name">Dentures</span><span class="svc-desc">Tooth pain is the 2nd most unbearable pain. It can be caused due to many reasons.</span><span class="arrow-dot">↗</span></div>
  <div class="pager"><span>←</span><span class="on">1</span><span>2</span><span>3</span><span>→</span></div>

  <!-- gallery -->
  <div class="abs eyebrow" style="left:19px;top:752px">See the transformation</div>
  <div class="abs h2" style="left:19px;top:759px">Smile Gallery</div>
  <div class="abs small" style="left:200px;top:752px;width:108px">The dream of having a perfect smile isn't far-fetched. We'll be happy to contribute in giving you a smile that you love and a smile that you can feel confident in.</div>
  <div class="abs" style="left:-2px;top:838px;font-size:16px;font-weight:700;color:#d6ecee;width:400px;line-height:1.2">REAL RESU<span style="margin-left:180px">REAL RES</span></div>
  <div class="photo" style="left:75px;top:790px;width:180px;height:102px;border-radius:4px;background:#b89a87;opacity:.6"></div>
  <div class="photo" style="left:84px;top:785px;width:160px;height:110px;border-radius:4px 4px 0 0;background:linear-gradient(90deg,#d9b79c 0%,#e9cdb5 50%,#f1dac6 100%)" role="img" aria-label="Before and after teeth whitening smile comparison"></div>
  <div class="abs" style="left:164px;top:785px;width:.6px;height:110px;background:#fff"></div>
  <div class="abs" style="left:88px;top:884px;font-size:3.4px;background:rgba(255,255,255,.8);padding:1px 3px;border-radius:1px">Before</div>
  <div class="abs" style="left:226px;top:884px;font-size:3.4px;background:rgba(255,255,255,.8);padding:1px 3px;border-radius:1px">After</div>
  <div class="abs" style="left:84px;top:895px;width:160px;height:31px;background:var(--soft);text-align:center;padding-top:8px">
    <div style="font-size:3.6px;color:var(--accent)">TREATMENTS</div>
    <div style="font-size:5.6px;font-weight:500;margin-top:3px">Teeth Whitening</div>
  </div>
  <div class="abs" style="left:153px;top:942px;display:flex;gap:2px"><span style="width:4px;height:1.5px;background:#cfd8da"></span><span style="width:8px;height:1.5px;background:var(--accent)"></span><span style="width:4px;height:1.5px;background:#cfd8da"></span></div>

  <!-- why -->
  <div class="band soft" style="top:965px;height:119px"></div>
  <div class="abs eyebrow" style="left:19px;top:987px">See the difference by yourself</div>
  <div class="abs h2" style="left:19px;top:994px">Why choose us?</div>
  <div class="abs small" style="left:200px;top:987px;width:108px">We have built an environment of trust and comfort with our patients by using the latest technology and providing best services in cost efficient way.</div>
  <div class="abs" style="left:19px;top:1027px;width:96px">
    <div style="width:14px;height:14px;border-radius:3px;background:var(--teal)"></div>
    <div style="font-size:4.6px;font-weight:600;margin:9px 0 3px">High Standard of Dentistry</div>
    <div class="small">We provide excellent dentistry experience by using latest technology.</div>
  </div>
  <div class="abs" style="left:123px;top:1027px;width:90px">
    <div style="width:14px;height:14px;border-radius:3px;background:var(--teal)"></div>
    <div style="font-size:4.6px;font-weight:600;margin:9px 0 3px">Committed Dental Team</div>
    <div class="small">We are a dedicated team of dentists who are passionate about what they do.</div>
  </div>
  <div class="abs" style="left:226px;top:1027px;width:82px">
    <div style="width:14px;height:14px;border-radius:3px;background:var(--teal)"></div>
    <div style="font-size:4.6px;font-weight:600;margin:9px 0 3px">Modern Equipments</div>
    <div class="small">The key to provide better dentistry experience is to evolve with time.</div>
  </div>

  <!-- achievements -->
  <div class="abs eyebrow" style="left:19px;top:1106px">Clinic figures</div>
  <div class="abs h2" style="left:19px;top:1113px">Our achievements so far!</div>
  <div class="abs small" style="left:200px;top:1106px;width:108px">We have built an environment of trust and comfort with our patients by using the latest technology and providing best services in cost efficient way.</div>
  <div class="stat pic" style="left:19px;top:1142px"><div class="photo" style="inset:0" role="img" aria-label="Smiling woman at the dentist"></div></div>
  <div class="stat" style="left:93px;top:1142px"><div class="lbl">Brighter Smiles Achieved</div></div>
  <div class="stat pic" style="left:167px;top:1142px"><div class="photo" style="inset:0" role="img" aria-label="Young man during a dental check-up"></div></div>
  <div class="stat" style="left:242px;top:1142px"><div class="lbl">Satisfied Patients and Counting</div></div>
</section>

<section class="col col-right">
  <div class="abs eyebrow" style="left:19px;top:20px">Clinic figures</div>
  <div class="abs h2" style="left:19px;top:26px">Our achievements so far!</div>
  <div class="abs small" style="left:199px;top:20px;width:109px">We have built an environment of trust and comfort with our patients by using the latest technology and providing best services in cost efficient way.</div>
  <div class="stat pic" style="left:19px;top:54px"><div class="photo" style="inset:0" role="img" aria-label="Smiling woman at the dentist"></div></div>
  <div class="stat" style="left:93px;top:54px"><div class="lbl">Brighter Smiles Achieved</div><div class="num">500+</div></div>
  <div class="stat pic" style="left:168px;top:54px"><div class="photo" style="inset:0" role="img" aria-label="Young man during a dental check-up"></div></div>
  <div class="stat" style="left:242px;top:54px"><div class="lbl">Satisfied Patients and Counting</div><div class="num">8k+</div></div>
  <div class="stat" style="left:19px;top:125px"><div class="lbl">Successful Root Canal Treatments</div><div class="num">2500+</div></div>
  <div class="stat pic" style="left:93px;top:125px"><div class="photo" style="inset:0" role="img" aria-label="Dentist treating a reclining patient"></div></div>
  <div class="stat" style="left:168px;top:125px"><div class="lbl">Successful Implant Surgeries</div><div class="num">750+</div></div>
  <div class="stat pic" style="left:242px;top:125px"><div class="photo" style="inset:0" role="img" aria-label="Dental team performing a procedure"></div></div>

  <div class="band soft" style="top:209px;height:211px"></div>
  <div class="member" style="left:19px;top:230px"><div class="av" role="img" aria-label="Portrait of team member"></div><b>Dr. Dorian Whitcombe</b><i>Owner and director</i></div>
  <div class="member" style="left:89px;top:230px"><div class="av" role="img" aria-label="Portrait of team member"></div><b>Maren Talbot</b><i>MDS,Oral &amp; Maxillofacial Surgery</i></div>
  <div class="member" style="left:19px;top:290px"><div class="av" role="img" aria-label="Portrait of team member"></div><b>Elise Hartwell</b><i>MDS,Oral Medicine And Radiology</i></div>
  <div class="member" style="left:89px;top:290px"><div class="av" role="img" aria-label="Portrait of team member"></div><b>Rowan Sellers</b><i>MDS,Oral &amp; Maxillofacial Surgery</i></div>
  <div class="member" style="left:19px;top:350px"><div class="av" role="img" aria-label="Portrait of team member"></div><b>Lionel Ashby</b><i>MDS,Oral Medicine And Radiology</i></div>
  <div class="member" style="left:89px;top:350px"><div class="av" role="img" aria-label="Portrait of team member"></div><b>Jonah Wexley</b><i>MDS,Oral &amp; Maxillofacial Surgery</i></div>
  <div class="faq">
    <div style="font-size:10px;font-weight:600;line-height:1.4">Frequently Asked Questions</div>
    <div style="display:flex;justify-content:space-between;font-size:4.6px;color:var(--accent);margin-top:8px"><span>Will scaling weaken my teeth?</span><span>−</span></div>
    <div class="small" style="margin:4px 0 7px">No, Scaling removes calculus and dirt deposited on your tooth making your gums healthy to hold your tooth for a longer time.</div>
    <div class="faq-q"><span>Are root canal treatment painful?</span><span>+</span></div>
    <div class="faq-q"><span>Are dental implants costly?</span><span>+</span></div>
    <div class="faq-q"><span>Are dental implants costly?</span><span>+</span></div>
    <div class="faq-q"><span>What if i dont get my missing teeth replaced?</span><span>+</span></div>
  </div>

  <div class="band" style="top:441px;height:172px;background:var(--teal)"></div>
  <div class="photo" style="left:0;top:441px;width:186px;height:172px;background:linear-gradient(135deg,#d9dcda,#b69379 55%,#dfe4e4)" role="img" aria-label="Happy woman giving a thumbs up in the dental chair"></div>
  <div class="abs" style="left:135px;top:441px;width:149px;height:136px;background:var(--white);border-radius:0 0 5px 5px;padding:15px 12px;overflow:hidden">
    <div style="position:absolute;left:12px;top:9px;font-size:14px;font-weight:700;color:#f4f6f6;line-height:1">Testimonials</div>
    <div class="eyebrow" style="position:relative">Testimonials</div>
    <div style="font-size:11.5px;font-weight:500;margin-top:11px;line-height:1.2">Our happy client says</div>
    <div style="display:flex;align-items:center;gap:4px;margin-top:7px"><div class="photo" style="position:static;width:12px;height:12px;border-radius:2px" role="img" aria-label="Client portrait"></div><div><div style="font-size:4.6px;font-weight:500">Alden Farrow</div><div style="font-size:3.4px;color:var(--text)">Los Angeles</div></div><div style="margin-left:auto;font-size:12px;color:var(--accent);font-weight:700;line-height:1">“</div></div>
    <div class="small" style="margin-top:6px">Cooperative staff, good quality treatment, came from rajkot for dental treatment because of my previous good experience before 4 years. Appointment time were followed with punctuality and no waiting time. The way doctor explain treatment plan was really excellent. Moreover overall treatment cost was economical.</div>
    <div style="display:flex;gap:4px;margin-top:6px"><span style="width:9px;height:9px;background:var(--accent);color:#fff;font-size:4px;display:flex;align-items:center;justify-content:center;border-radius:1px">←</span><span style="width:9px;height:9px;background:var(--accent);color:#fff;font-size:4px;display:flex;align-items:center;justify-content:center;border-radius:1px">→</span></div>
  </div>

  <div class="photo" style="left:19px;top:634px;width:141px;height:159px;border-radius:4px;background:linear-gradient(135deg,#d4c7c2,#c9927e 50%,#b43b5f)" role="img" aria-label="Woman holding a tooth shade guide to her smile"></div>
  <div class="abs" style="left:167px;top:634px;width:141px;height:159px;background:var(--teal);border-radius:4px;color:var(--white);padding:11px 12px;overflow:hidden">
    <div style="font-size:3.6px">We highly encourage</div>
    <div style="font-size:9.4px;font-weight:600;margin:2px 0 5px;line-height:1.2">Lorem Ipsum dummy text</div>
    <div style="font-size:3.4px;line-height:1.7;text-align:justify;opacity:.92">Lorem Ipsum is simply dummy text of the printing and typesetting industry. There are many variations of passages of Lorem Ipsum available, but the majority have suffered alteration in some form, by injected humour, or randomised words which don't look even slightly believable. If you are going to use a passage of Lorem Ipsum.<br><br>There are many variations of passages of Lorem Ipsum available, but the majority have suffered alteration in some form, by injected humour, or randomised words which don't look even slightly believable. If you are going to use a passage of Lorem Ipsum, you need to be sure there isn't anything embarrassing hidden in the middle of text. There are many variations of passages of Lorem Ipsum available, but the majority have suffered alteration in some form, by injected humour.<br><br>There are many variations of passages of Lorem Ipsum available, but the majority have suffered alteration in some form, by injected humour, or randomised words which don't look</div>
  </div>

  <div class="photo" style="left:0;top:814px;width:327px;height:163px;background:linear-gradient(135deg,#3c4448,#6f7a7e 45%,#2f3a30 80%,#4e6b3c)" role="img" aria-label="Modern dental treatment room with chair and equipment"></div>
  <svg class="abs" style="left:146px;top:888px" width="24" height="24" viewBox="0 0 24 24"><circle cx="12" cy="12" r="12" fill="#fff"/><path d="M9.5 7.5v9l7-4.5z" fill="#0f676b"/></svg>
  <div class="abs" style="left:19px;top:996px;font-size:9.6px;font-weight:500;line-height:1.3;width:120px">Schedule Your Appointment Now And Take The First Step</div>
  <div class="abs" style="left:155px;top:947px;width:153px;height:107px;background:var(--soft);border-radius:5px"></div>
  <div class="abs" style="left:164px;top:954px;font-size:9.6px;font-weight:500;line-height:1.2">Book For Consultation</div>
  <div class="flabel" style="left:164px;top:976px">Patient Name</div>
  <div class="flabel" style="left:234px;top:976px">Phone Number</div>
  <div class="field" style="left:164px;top:982px;width:64px">Enter here</div>
  <div class="field" style="left:234px;top:982px;width:64px">Enter here</div>
  <div class="flabel" style="left:164px;top:1003px">Visit Date/Time</div>
  <div class="flabel" style="left:234px;top:1003px">Choose Service</div>
  <div class="field" style="left:164px;top:1009px;width:64px"><span>Select</span><span>▭</span></div>
  <div class="field" style="left:234px;top:1009px;width:64px"><span>Select</span><span>⌄</span></div>
  <div class="btn" style="left:164px;top:1031px;width:52px;height:13px;background:var(--teal);color:var(--white);border-radius:7px">Book Appointment</div>

  <footer class="abs footer">
    <div class="abs" style="left:15px;top:11px;font-size:8px;font-weight:700;line-height:1.2">Harrowfield</div>
    <div class="abs" style="left:15px;top:32px;font-size:3.4px">Where amazing smiles begin!</div>
    <div class="abs" style="left:82px;top:11px"><h4>Quick link</h4><div class="list">About Us<br>Services<br>Case studies<br>Testimonials<br>Blogs<br>Smile Gallery</div></div>
    <div class="abs" style="left:134px;top:11px;width:68px"><h4>Contact us</h4><div style="font-size:3.4px;line-height:1.7">418 Larkspur Ave. Fairmont, Ohio 44021<br><span style="line-height:2.8">☏ (310) 555-0184</span><br>✉ hello@harrowfielddental.com</div></div>
    <div class="abs" style="left:207px;top:11px"><h4>Clinic Timing</h4><div style="font-size:3.4px;line-height:2.6">Mon to Sat 9:00 am to 12:30 pm<br>Mon to Sat 5:00 pm to 8:30 pm</div></div>
    <div class="abs" style="left:15px;right:15px;top:89px;height:.5px;background:rgba(255,255,255,.3)"></div>
    <div class="abs" style="left:15px;top:96px;font-size:3.4px">Copyright © 2021 Harrowfield Dentistry</div>
    <div class="abs" style="right:15px;top:96px;font-size:3.4px">For emergency cases (310) 555-0184</div>
  </footer>
</section>

</body>
</html>
```